Young, dynamic furniture company needs a new business card design

We require a new business card design for our modern furniture company which supplies furniture and appliances to the property and development market.
Oakridge Interiors has become one of the leading furniture & appliance suppliers to the property market withing London. With over 10 years experience, we have increased our business to supply not only private landlords and managing agents, but also property developers, housing associations and local councils.
We offer not only a complete range of furniture which includes beds, wardrobes, dining sets and sofas, but also a high quality, full delivery and assembly service to help you with all our furnishing needs.

Target Market(s)

Private landlords, estate agents, letting agents, property management companies

Industry/Entity Type

Business

Contact Information for Business Card

Name,
Title,
Address,
Mobile,
Telephone,
Fax, Website, email address

Font styles to use
Sans Serif

Colors
3176b5
0555a3
85abd2
cfdeed

Requirements
Must have
• All the above information for each of our staff, along with our logo

```html
<!DOCTYPE html>
<html lang="en">
<head>
<meta charset="utf-8">
<title>Oakridge Interiors – Business Card</title>
<link rel="stylesheet" href="https://fonts.googleapis.com/css2?family=Open+Sans:wght@400;700&family=Roboto:wght@300;400&display=swap">
<style>
  :root {
    --stage: #1d1d1f;
    --blue-deep: #0555a3;
    --blue-mid: #3176b5;
    --blue-light: #85abd2;
    --blue-pale: #cfdeed;
    --navy: #0f3566;
    --ink: #1a1a1a;
    --grey: #5a5a5e;
    --white: #ffffff;
  }
  * { box-sizing: border-box; margin: 0; padding: 0; }
  html, body { width: 1200px; height: 923px; overflow: hidden; background: var(--stage); }
  .stage { position: relative; width: 1200px; height: 923px; }

  .card {
    position: absolute;
    width: 640px; height: 366px;
    border-radius: 22px;
    overflow: hidden;
  }

  /* Back side */
  .card-back {
    left: 500px; top: 60px;
    background: radial-gradient(ellipse at 55% 40%, #1a64ad 0%, #12457f 45%, var(--navy) 100%);
    color: var(--white);
    text-align: center;
    font-family: "Roboto", sans-serif;
  }
  .card-back .brand { position: absolute; left: 0; right: 0; top: 120px; }
  .card-back .brand-name {
    font-weight: 400; font-size: 38px; letter-spacing: 1px; text-transform: uppercase;
  }
  .card-back .brand-tagline {
    margin-top: 6px; font-weight: 300; font-size: 15px; letter-spacing: 1.5px; text-transform: uppercase;
  }
  .card-back .website {
    position: absolute; left: 0; right: 0; bottom: 58px;
    font-family: "Open Sans", sans-serif; font-size: 17px;
  }

  /* Front side */
  .card-front { left: 60px; top: 497px; background: var(--white); }
  .card-front .swoosh { position: absolute; inset: 0; }
  .card-front .brand {
    position: absolute; left: 30px; top: 112px;
    font-family: "Roboto", sans-serif; color: var(--ink);
  }
  .card-front .brand-mark-row { display: flex; align-items: center; gap: 10px; }
  .card-front .brand-square { width: 22px; height: 22px; background: var(--blue-mid); flex: none; }
  .card-front .brand-name {
    font-weight: 400; font-size: 24px; letter-spacing: 0.5px; text-transform: uppercase; white-space: nowrap;
  }
  .card-front .brand-tagline {
    margin-top: 6px; margin-left: 32px; font-weight: 300; font-size: 12px;
    letter-spacing: 1.2px; text-transform: uppercase; color: var(--grey);
  }
  .card-front .divider {
    position: absolute; left: 350px; top: 60px; width: 1.5px; height: 170px;
    background: linear-gradient(to bottom, rgba(49,118,181,0), var(--blue-mid) 40%, rgba(49,118,181,0));
  }
  .contact {
    position: absolute; left: 378px; top: 50px;
    font-family: "Open Sans", sans-serif; color: var(--ink); font-size: 15px; line-height: 1.45;
  }
  .contact .person-name { font-weight: 700; font-size: 19px; color: var(--blue-deep); line-height: 1.2; }
  .contact .job-title { margin-bottom: 8px; }
  .contact .address { margin-bottom: 6px; }
  .contact ul { list-style: none; }
  .contact li { display: flex; align-items: center; gap: 9px; }
  .contact li svg { width: 14px; height: 14px; fill: var(--blue-deep); flex: none; }
  .card-front .website {
    position: absolute; right: 44px; bottom: 12px;
    font-family: "Open Sans", sans-serif; font-size: 17px; color: var(--white);
  }
</style>
</head>
<body>
<main class="stage">

  <section class="card card-back" aria-label="Business card back">
    <div class="brand">
      <div class="brand-name">Oakridge Interiors</div>
      <div class="brand-tagline">Trade Furniture Solutions</div>
    </div>
    <div class="website">www.oakridgeinteriors.com</div>
  </section>

  <section class="card card-front" aria-label="Business card front">
    <svg class="swoosh" viewBox="0 0 640 366" preserveAspectRatio="none" aria-hidden="true">
      <defs>
        <linearGradient id="band-fill" x1="0" y1="0" x2="1" y2="0">
          <stop offset="0" stop-color="#0555a3"/>
          <stop offset="0.45" stop-color="#85abd2"/>
          <stop offset="0.7" stop-color="#3176b5"/>
          <stop offset="1" stop-color="#0555a3"/>
        </linearGradient>
        <linearGradient id="line-fade" x1="0" y1="0" x2="1" y2="0">
          <stop offset="0" stop-color="#5a5a5e"/>
          <stop offset="0.8" stop-color="#5a5a5e"/>
          <stop offset="1" stop-color="#5a5a5e" stop-opacity="0"/>
        </linearGradient>
      </defs>
      <path d="M0 222 C150 280 320 296 450 302 C540 306 600 312 640 322 L640 366 L0 366 Z" fill="url(#band-fill)"/>
      <path d="M0 200 C150 262 300 282 430 292" fill="none" stroke="url(#line-fade)" stroke-width="5"/>
      <path d="M0 212 C150 272 300 290 430 298" fill="none" stroke="#ffffff" stroke-width="3"/>
    </svg>

    <div class="brand">
      <div class="brand-mark-row">
        <span class="brand-square"></span>
        <span class="brand-name">Oakridge Interiors</span>
      </div>
      <div class="brand-tagline">Trade Furniture Solutions</div>
    </div>

    <div class="divider"></div>

    <div class="contact">
      <div class="person-name">Daniel Reed</div>
      <div class="job-title">Job Title</div>
      <div class="address">34 Street Name<br>City Name, Country 4567</div>
      <ul>
        <li><svg viewBox="0 0 16 16"><path d="M3 2l3 0 1 4-2 1c1 2 2 3 4 4l1-2 4 1 0 3c-7 1-12-4-11-11z"/></svg>000 1234 5678</li>
        <li><svg viewBox="0 0 16 16"><path d="M4 1h8v14H4z M6 3v9h4V3z"/></svg>000 1234 5678</li>
        <li><svg viewBox="0 0 16 16"><path d="M4 1h8v4H4z M1 6h14v6h-3v3H4v-3H1z M5 10v4h6v-4z"/></svg>000 1234 5678</li>
        <li><svg viewBox="0 0 16 16"><path d="M1 3h14v10H1z M2 4l6 5 6-5z" fill-rule="evenodd"/></svg>info@oakridgeinteriors.com</li>
      </ul>
    </div>

    <div class="website">www.oakridgeinteriors.com</div>
  </section>

</main>
</body>
</html>
```